A3 Poster & DL Flyer Design Project

We need a poster and flyer designed to advertise a Wine, Food and Live music event.
Event title is "A Sip of Fine Moments" and is put on by Harlow's Creek Wines. Date for the event is Sunday 21 April 2013
The outdoor event covers wine, gourmet food and live music
Live music genera is Jazz, Blues, Swing
Updates

Project Deadline Extended
Reason: Most of the designs did not meet our requirements only 3 out of 21 have potential but would like to see more

Target Market(s)

25 - 55 wine drinkers with money.

Industry/Entity Type

Event

Requirements
Must have
• Title of the Event "A Sip of Fine Moments"
Date Sunday 21 April 2013 or be generic where we can write the date on each year.
Heron Logo
Entry is Free
No BYO Alcohol
Must reflect Wine, Food & Live Music

```html
<!DOCTYPE html>
<html lang="en">
<head>
<meta charset="utf-8">
<title>A Sip of Fine Moments – Harlow's Creek Wines</title>
<link rel="stylesheet" href="https://fonts.googleapis.com/css2?family=Arimo:wght@400;500;700&family=Archivo+Narrow:wght@600&family=Tinos:wght@400;700&display=swap">
<style>
  :root {
    --backdrop: #efeeec;
    --logo-dark: #3b2519;
    --logo-light: #d9d2cc;
    --sky-blue: #6a9fb3;
    --sky-blue-deep: #588da2;
    --name-bar: #d8cdcb;
    --name-ink: #3a2a24;
    --wood-dark: #4a2212;
    --wood-mid: #7a3a1c;
    --wood-light: #95502a;
    --title-ink: #f4ece4;
    --curtain-deep: #2a0d0a;
    --curtain-red: #6e1e14;
    --plank-light: #d9b98e;
    --plank-dark: #b88d5c;
    --plank-ink: #24150c;
    --rope: #c9a877;
    --badge-red: #a3232b;
    --badge-ring: #c9c5c3;
    --badge-ink: #ffffff;
  }
  * { margin: 0; padding: 0; box-sizing: border-box; }
  html, body { width: 1200px; height: 882px; overflow: hidden; background: var(--backdrop); }

  .poster {
    position: absolute; left: 330px; top: 21px;
    width: 541px; height: 840px; overflow: hidden;
    background: var(--curtain-deep);
    box-shadow: 0 2px 8px rgba(0,0,0,.25);
  }

  .masthead { position: absolute; left: 0; top: 0; width: 541px; height: 98px; display: flex; }
  .brand-mark {
    width: 211px; height: 98px; background: var(--logo-dark);
    display: flex; align-items: center; gap: 10px; padding-left: 18px;
    font-family: "Tinos", serif; font-size: 17px; color: var(--logo-light);
  }
  .brand-mark .dot { width: 14px; height: 14px; border-radius: 50%; background: var(--logo-light); flex: none; }
  .sky-art { flex: 1; background: linear-gradient(160deg, var(--sky-blue), var(--sky-blue-deep)); }

  .name-bar {
    position: absolute; left: 0; top: 98px; width: 541px; height: 28px;
    background: var(--name-bar); text-align: right; padding-right: 10px;
    font-family: "Tinos", serif; font-size: 18px; letter-spacing: 1.5px;
    line-height: 28px; color: var(--name-ink); text-transform: uppercase;
  }

  .title-board {
    position: absolute; left: 0; top: 126px; width: 541px; height: 216px;
    background: linear-gradient(90deg, var(--wood-dark), var(--wood-mid) 30%, var(--wood-light) 55%, var(--wood-mid) 80%, var(--wood-dark));
    border-bottom: 3px solid #2c120a;
    text-align: center; color: var(--title-ink);
    font-family: "Arimo", sans-serif; text-shadow: 0 2px 3px rgba(0,0,0,.45);
  }
  .title-board h1 { font-weight: 400; }
  .title-board .line {
    position: absolute; left: 0; width: 100%;
    font-size: 54px; line-height: 70px; white-space: nowrap;
  }
  .title-board .line-1 { top: 13px; }
  .title-board .line-2 { top: 94px; }
  .title-board .big { font-size: 66px; font-weight: 500; }
  .title-board .host {
    position: absolute; left: 0; top: 169px; width: 100%;
    font-size: 28px; line-height: 34px;
  }

  .stage {
    position: absolute; left: 0; top: 342px; width: 541px; height: 498px;
    background: linear-gradient(90deg, var(--curtain-deep), var(--curtain-red) 45%, var(--curtain-deep));
  }
  .still-life {
    position: absolute; left: 288px; top: 27px; width: 253px; height: 471px;
    background: radial-gradient(ellipse at 45% 45%, #c99b52 0%, #7a5a2a 35%, #4a4a24 65%, #2a1a10 100%);
  }

  .ropes { position: absolute; left: 0; top: 0; width: 330px; height: 320px; }

  .plank {
    position: absolute; height: 42px; border-radius: 4px;
    background: linear-gradient(180deg, var(--plank-light), var(--plank-dark));
    box-shadow: 0 3px 4px rgba(0,0,0,.45);
    font-family: "Archivo Narrow", sans-serif; font-weight: 600; font-size: 28px;
    color: var(--plank-ink); text-align: center; line-height: 42px; white-space: nowrap;
  }
  .plank-wine    { left: 33px; top: 28px;  width: 259px; }
  .plank-food    { left: 33px; top: 88px;  width: 276px; }
  .plank-music   { left: 33px; top: 147px; width: 259px; }
  .plank-entry   { left: 24px; top: 204px; width: 267px; }
  .plank-byo     { left: 24px; top: 263px; width: 270px; }

  .date-badge {
    position: absolute; left: 76px; top: 322px; width: 155px; height: 155px;
    border-radius: 50%; background: var(--badge-red);
    border: 7px solid var(--badge-ring);
    box-shadow: 0 3px 6px rgba(0,0,0,.5);
    display: flex; flex-direction: column; align-items: center; justify-content: center;
    font-family: "Tinos", serif; font-weight: 700; color: var(--badge-ink);
    font-size: 27px; line-height: 1.15;
  }
  .date-badge sup { font-size: 15px; }
</style>
</head>
<body>
  <main class="poster">
    <header class="masthead">
      <div class="brand-mark"><span class="dot"></span>Harlow's Creek Wines</div>
      <div class="sky-art" role="img" aria-label="Blue panel with white reed strokes"></div>
    </header>
    <div class="name-bar">Harlow's Creek Wines</div>

    <section class="title-board">
      <h1>
        <span class="line line-1">A <span class="big">Sip</span></span>
        <span class="line line-2">of <span class="big">Fine</span> Moments</span>
      </h1>
      <span class="host">by Harlow's Creek Wines</span>
    </section>

    <section class="stage">
      <div class="still-life" role="img" aria-label="Photo of a glass of white wine, a wine bottle and green grapes"></div>

      <svg class="ropes" viewBox="0 0 330 320" aria-hidden="true">
        <g stroke="var(--rope)" stroke-width="3">
          <line x1="70" y1="0" x2="70" y2="317"/>
          <line x1="259" y1="0" x2="259" y2="317"/>
        </g>
      </svg>

      <ul class="signpost" style="list-style:none;">
        <li class="plank plank-wine">Wine</li>
        <li class="plank plank-food">Gourmet Food</li>
        <li class="plank plank-music">Live Music</li>
        <li class="plank plank-entry">Entry is Free</li>
        <li class="plank plank-byo">No BYO Alcohol</li>
      </ul>

      <div class="date-badge"><span>21<sup>st</sup></span><span>APRIL</span><span>2013</span></div>
    </section>
  </main>
</body>
</html>
```